Business card design needed with logo

My business is called PLQ Works & it is targeted towards mobile equipment maintenance in the Mining and civil industry. My work involves maintenance planning and maintenance management plus also supply tradespeople on a labour hire basis. We can provide from basic shut-down machine rebuild plans to complete rebuild services supply plans and labour to anywhere in Australia. I would like to use the colours Black, Red and Grey, I had done a desgin as attached but doesn't really explain what we do and gears don't embroider well onto shirts.
Updates

I also wanted to see the something replace the gears maybe just making the PLQ lettering look a bit different or put together differently 

Hello I have extended the deadline by a few extra days as I would like to update details on the front of card, details below & can be put which ever way looks good;

Mark Tilley
Director
0417295361
PLQ@mailbay.com.au
www.plqworks-example.com.au

On the back of the card I would like to have the below printed;

Capable of providing, but not limited to, across Australia:
- Contract Maintenance Planning.
- Skilled Mobile Maintenance labour hire.
- New machine build specifications. 
- Plant risk assessments and inspections.
- Shut down and rebuild program planning.
- Preventative maintenance tasks, including build of materials lists, creation and review.

Target Market(s)

Contractors and companies that use small and large earthmoving and mining machines

Industry/Entity Type

Business

Contact Information for Business Card

Trading name is PLQ Works
My name and title is
Mark Tilley Director
0417 295 361
PLQ@mailbay.com.au

Logo Text

PLQ

```html
<!DOCTYPE html>
<html lang="en">
<head>
<meta charset="utf-8">
<title>PLQ Works — Business Card</title>
<link rel="stylesheet" href="https://fonts.googleapis.com/css2?family=PT+Sans+Narrow:wght@400;700&family=Ubuntu:wght@400;500&display=swap">
<style>
  :root {
    --paper: #ffffff;
    --ink: #000000;
    --grey: #a3a3a3;
    --grey-soft: #b8b8b8;
    --red: #e2001a;
    --edge: #6e6e6e;
  }
  html, body {
    margin: 0;
    padding: 0;
    width: 1200px;
    height: 849px;
    overflow: hidden;
    background: var(--paper);
  }
  .canvas {
    position: relative;
    width: 1200px;
    height: 849px;
  }
  .card {
    position: absolute;
    top: 279px;
    width: 430px;
    height: 246px;
    display: block;
  }
  .card--front { left: 134px; }
  .card--back { left: 622px; }
  .brand-mark {
    font-family: "Ubuntu", sans-serif;
    font-weight: 500;
    fill: var(--red);
  }
  .brand-name {
    font-family: "Ubuntu", sans-serif;
    font-weight: 500;
    fill: var(--red);
  }
  .contact {
    font-family: "PT Sans Narrow", sans-serif;
    fill: var(--ink);
  }
  .contact--name { font-size: 16px; }
  .contact--role { font-size: 9px; }
  .contact--line { font-size: 10px; }
</style>
</head>
<body>
<main class="canvas">

  <!-- Front of card -->
  <svg class="card card--front" viewBox="0 0 415 238" aria-label="Front of business card">
    <defs>
      <clipPath id="front-shape"><rect x="0.5" y="0.5" width="414" height="237" rx="12" ry="12"/></clipPath>
      <linearGradient id="front-gear-tone" x1="0" y1="0" x2="0" y2="1">
        <stop offset="0" stop-color="#2a2a2a"/>
        <stop offset="1" stop-color="#161616"/>
      </linearGradient>
    </defs>
    <g clip-path="url(#front-shape)">
      <rect class="card__paper" width="415" height="238" fill="var(--paper)"/>
      <polygon class="card__chevron" points="325,0 350,0 380,55 270,238 245,238 355,55" fill="var(--grey)"/>
      <polygon class="card__panel" points="350,0 415,0 415,238 270,238 380,55" fill="var(--ink)"/>
      <rect class="card__gear-art" x="328" y="106" width="72" height="132" fill="url(#front-gear-tone)" role="img" aria-label="Outline drawing of two interlocking gears"/>
    </g>
    <rect x="0.5" y="0.5" width="414" height="237" rx="12" ry="12" fill="none" stroke="var(--edge)" stroke-width="0.8"/>

    <text class="brand-name" x="25" y="86" font-size="20">PLQ Works</text>
    <text class="brand-mark" x="170" y="82" font-size="60">PLQ</text>

    <text class="contact contact--name" x="24" y="154">Mark Tilley</text>
    <line class="contact__rule" x1="24" y1="158" x2="190" y2="158" stroke="var(--red)" stroke-width="0.6"/>
    <text class="contact contact--role" x="24" y="170">Director</text>

    <g class="icon icon--phone" fill="var(--red)">
      <path d="M25.5 185.5c.6-.6 1.3-.6 1.7 0l.8 1.2c.3.5.2 1-.2 1.3l-.5.4c.4 1 1.1 1.8 2.1 2.2l.4-.5c.3-.4.9-.5 1.3-.2l1.2.8c.5.4.5 1.1 0 1.6l-.7.7c-2.6.6-6.8-3.7-6.3-6.4z"/>
    </g>
    <text class="contact contact--line" x="46" y="192">0417 295 361</text>

    <g class="icon icon--mail">
      <rect x="24" y="203" width="8.5" height="5.5" rx="0.6" fill="var(--red)"/>
      <polyline points="24.6,203.6 28.25,206.4 31.9,203.6" fill="none" stroke="var(--paper)" stroke-width="0.7"/>
    </g>
    <text class="contact contact--line" x="46" y="209">e-mail : PLQ@mailbay.com.au</text>
  </svg>

  <!-- Back of card -->
  <svg class="card card--back" viewBox="0 0 415 238" aria-label="Back of business card">
    <defs>
      <clipPath id="back-shape"><rect width="415" height="238" rx="12" ry="12"/></clipPath>
      <linearGradient id="back-gear-tone" x1="0" y1="0" x2="1" y2="1">
        <stop offset="0" stop-color="var(--grey-soft)"/>
        <stop offset="1" stop-color="var(--grey)"/>
      </linearGradient>
    </defs>
    <g clip-path="url(#back-shape)">
      <rect class="card__panel-grey" width="415" height="238" fill="var(--grey)"/>
      <rect class="card__gear-art" x="0" y="0" width="128" height="238" fill="url(#back-gear-tone)" role="img" aria-label="Large outline drawing of two interlocking gears"/>
      <polygon class="card__panel" points="148,0 415,0 415,238 68,238 178,55" fill="var(--ink)"/>
    </g>
    <text class="brand-mark" x="174" y="82" font-size="60">PLQ</text>
    <text class="brand-name" x="166" y="118" font-size="20">PLQ Works</text>
  </svg>

</main>
</body>
</html>
```